RTavenor Business Cards & Letterhead

I have a logo but need a design for some new business cards. We are a Design-Build Firm that specializes in the design and construction of commercial projects.
the cards need to be professional. no cartoon stuff.
i would like to have the cards in AI format so I can update the card as needed. Logo is provided.
Our Address is: 4187 Marlowe Ct. Brookhaven, Oregon 27614

```html
<!DOCTYPE html>
<html lang="en">
<head>
<meta charset="utf-8">
<title>RTavenor Business Card</title>
<link href="https://fonts.googleapis.com/css2?family=Open+Sans:wght@400;600;700&display=swap" rel="stylesheet">
<style>
  :root {
    --backdrop: #474747;
    --card: #ffffff;
    --brand-blue: #0a62a8;
    --brand-blue-dark: #0b4a86;
    --ink: #2b2b2b;
    --logo-grey: #6b6b6b;
  }
  * { box-sizing: border-box; margin: 0; padding: 0; }
  html, body {
    width: 1200px; height: 801px; overflow: hidden;
    background: var(--backdrop);
    font-family: "Open Sans", sans-serif;
  }
  .stage {
    position: relative; width: 1200px; height: 801px;
    display: flex; align-items: center; justify-content: center; gap: 40px;
  }
  .card {
    position: relative; width: 540px; height: 310px;
    background: var(--card); border-radius: 14px; overflow: hidden;
  }
  .card-front { border-bottom: 3px solid var(--brand-blue); }

  .identity {
    position: absolute; left: 60px; top: 108px; text-align: right; width: 220px;
  }
  .identity-name {
    color: var(--brand-blue); font-weight: 700; font-size: 22px;
    letter-spacing: 0.5px; line-height: 1.1;
  }
  .identity-title { color: var(--ink); font-size: 15px; margin-top: 4px; }

  .divider {
    position: absolute; left: 295px; top: 100px; width: 1.5px; height: 72px;
    background: var(--brand-blue);
  }

  .contacts {
    position: absolute; left: 312px; top: 96px; list-style: none;
    color: var(--ink); font-size: 13px; line-height: 26px;
  }
  .contacts li { display: flex; align-items: center; gap: 7px; }
  .contacts svg { width: 12px; height: 12px; fill: var(--brand-blue); flex: none; }

  .address-band {
    position: absolute; left: 0; right: 0; top: 232px; height: 32px;
    background: linear-gradient(180deg, var(--brand-blue) 0%, var(--brand-blue-dark) 100%);
    color: #fff; font-size: 14px; line-height: 32px; padding-left: 150px;
    letter-spacing: 0.3px; white-space: nowrap;
  }

  .card-back { display: flex; align-items: center; justify-content: center; }
  .wordmark { display: flex; align-items: center; gap: 12px; }
  .wordmark-square { width: 30px; height: 30px; background: var(--brand-blue); }
  .wordmark-name {
    color: var(--logo-grey); font-weight: 700; font-size: 46px; letter-spacing: 1px;
  }
</style>
</head>
<body>
<main class="stage">
  <section class="card card-front">
    <div class="identity">
      <p class="identity-name">DANIEL WHITFIELD</p>
      <p class="identity-title">Managing Director</p>
    </div>
    <div class="divider"></div>
    <ul class="contacts">
      <li>
        <svg viewBox="0 0 24 24" aria-hidden="true"><path d="M6.6 10.8a15.1 15.1 0 0 0 6.6 6.6l2.2-2.2a1 1 0 0 1 1-.25 11.4 11.4 0 0 0 3.6.57 1 1 0 0 1 1 1V20a1 1 0 0 1-1 1A17 17 0 0 1 3 4a1 1 0 0 1 1-1h3.5a1 1 0 0 1 1 1c0 1.250.2 2.450.57 3.57a1 1 0 0 1-.25 1z"/></svg>
        919 555 0142
      </li>
      <li>
        <svg viewBox="0 0 24 24" aria-hidden="true"><path d="M2 5h20v14H2zM3.5 6.5 12 13l8.5-6.5z"/></svg>
        info@rtavenor-build.com
      </li>
      <li>
        <svg viewBox="0 0 24 24" aria-hidden="true"><circle cx="12" cy="12" r="10"/><path d="M2 12h20M12 2c3 3 3 17 0 20M12 2c-3 3-3 17 0 20" stroke="#fff" stroke-width="1.5" fill="none"/></svg>
        www.rtavenor-build.com
      </li>
    </ul>
    <div class="address-band">4187 Marlowe Ct. Brookhaven, Oregon 27614</div>
  </section>

  <section class="card card-back">
    <div class="wordmark">
      <span class="wordmark-square"></span>
      <span class="wordmark-name">RTAVENOR</span>
    </div>
  </section>
</main>
</body>
</html>
```